RTavenor Business Cards & Letterhead

I have a logo but need a design for some new business cards. We are a Design-Build Firm that specializes in the design and construction of commercial projects.
the cards need to be professional. no cartoon stuff.
i would like to have the cards in AI format so I can update the card as needed. Logo is provided.
Our Address is: 4187 Marlowe Ct. Apex, North Carolina 27614

```html
<!DOCTYPE html>
<html lang="en">
<head>
<meta charset="utf-8">
<title>RTavenor Business Card</title>
<link href="https://fonts.googleapis.com/css2?family=Figtree:wght@400;700;800&display=swap" rel="stylesheet">
<style>
  :root {
    --page-bg: #e4e4e3;
    --card-dark-a: #616367;
    --card-dark-b: #838487;
    --card-light-a: #e3e3e4;
    --card-light-b: #f5f5f6;
    --brand-blue: #175d97;
    --ink-dark: #48494c;
    --ink-text: #505155;
    --rule: #5a5b5e;
  }
  * { margin: 0; padding: 0; box-sizing: border-box; }
  html, body { width: 1200px; height: 1200px; overflow: hidden; }
  body {
    background: var(--page-bg);
    font-family: "Figtree", Arial, sans-serif;
    position: relative;
  }
  .card {
    position: absolute;
    left: 234px;
    width: 731px;
    height: 417px;
  }
  .card-front {
    top: 160px;
    background: linear-gradient(120deg, var(--card-dark-a), var(--card-dark-b));
  }
  .card-back {
    top: 632px;
    background: linear-gradient(120deg, var(--card-light-a), var(--card-light-b));
  }
  .brand {
    position: absolute;
    display: flex;
    align-items: center;
    color: var(--ink-dark);
    font-weight: 800;
    letter-spacing: 0.01em;
    line-height: 1;
  }
  .brand-square { background: var(--brand-blue); flex: none; }
  .card-front .brand { left: 118px; top: 183px; font-size: 72px; gap: 14px; }
  .card-front .brand-square { width: 56px; height: 56px; }
  .card-back .brand { left: 84px; top: 196px; font-size: 40px; gap: 8px; }
  .card-back .brand-square { width: 30px; height: 30px; }
  .divider {
    position: absolute;
    left: 377px; top: 102px;
    width: 2px; height: 212px;
    background: var(--rule);
  }
  .contact {
    position: absolute;
    left: 404px; top: 98px;
    color: var(--ink-text);
    font-size: 19px;
    line-height: 1.4;
  }
  .contact-name { color: var(--brand-blue); font-size: 31px; font-weight: 700; line-height: 1.1; }
  .contact-title { margin-top: 4px; }
  .contact-address { margin-top: 12px; }
  .contact-list { list-style: none; margin-top: 10px; }
  .contact-list li { display: flex; align-items: center; gap: 10px; height: 28px; }
  .contact-list svg { width: 16px; height: 16px; fill: var(--brand-blue); flex: none; }
</style>
</head>
<body>
  <section class="card card-front">
    <div class="brand"><span class="brand-square"></span>RTAVENOR</div>
  </section>

  <section class="card card-back">
    <div class="brand"><span class="brand-square"></span>RTAVENOR</div>
    <div class="divider"></div>
    <div class="contact">
      <div class="contact-name">Marcus Ellery</div>
      <div class="contact-title">Founder &amp; Director</div>
      <div class="contact-address">4187 Marlowe Ct. Apex,<br>North Carolina 27614</div>
      <ul class="contact-list">
        <li><svg viewBox="0 0 24 24"><path d="M6.6 10.8a15 15 0 0 0 6.6 6.6l2.2-2.2c.3-.3.7-.4 1-.2 1.1.4 2.3.6 3.6.6.6 0 1 .4 1 1V20c0 .6-.4 1-1 1A17 17 0 0 1 3 4c0-.6.4-1 1-1h3.5c.6 0 1 .4 1 1 0 1.3.2 2.5.6 3.6.1.3 0 .7-.2 1z"/></svg>(405)-555-0147</li>
        <li><svg viewBox="0 0 24 24"><path d="M2 5h20v14H2zm2 2v.5l8 5 8-5V7z"/></svg>marcus@rtavenor.com</li>
        <li><svg viewBox="0 0 24 24"><path d="M12 2a10 10 0 1 0 0 20 10 10 0 0 0 0-20zm6.9 9h-3a15 15 0 0 0-1.3-5.6A8 8 0 0 1 18.9 11zM12 4c.9 1.2 1.8 3.7 1.9 7h-3.8c.1-3.3 1-5.8 1.9-7zM9.4 5.4A15 15 0 0 0 8.1 11h-3a8 8 0 0 1 4.3-5.6zM5.1 13h3a15 15 0 0 0 1.3 5.6A8 8 0 0 1 5.1 13zm6.9 7c-.9-1.2-1.8-3.7-1.9-7h3.8c-.1 3.3-1 5.8-1.9 7zm2.6-1.4a15 15 0 0 0 1.3-5.6h3a8 8 0 0 1-4.3 5.6z"/></svg>www.rtavenor.com</li>
      </ul>
    </div>
  </section>
</body>
</html>
```